Modern Business Card

Modern professional business card with more than just logo and demographic info. Something memorable.

We are a trendy/modern chiropractic group with an emphasis on neurology, hence the minimalist-type brain logo. We want to convey that modern and technical aspect with professionalism and the elite nature of our practice environment.

```html
<!DOCTYPE html>
<html lang="en">
<head>
<meta charset="utf-8">
<title>Meridian Spine – Business Card</title>
<link rel="stylesheet" href="https://fonts.googleapis.com/css2?family=Libre+Baskerville&family=Roboto+Slab:wght@700&family=Arimo&display=swap">
<style>
  :root {
    --backdrop: #2e2926;
    --card: #101010;
    --card-edge: #1c1c1c;
    --accent-blue: #4a86c8;
    --text-light: #d6d6d6;
    --text-muted: #bdbdbd;
    --silver: #e4e4e4;
    --divider: #2c2c2c;
  }
  * { margin: 0; padding: 0; box-sizing: border-box; }
  html, body { width: 1200px; height: 844px; overflow: hidden; }
  body {
    background: var(--backdrop);
    position: relative;
    font-family: "Arimo", Arial, sans-serif;
  }
  .card {
    position: absolute;
    width: 504px;
    height: 288px;
    background: var(--card);
    border: 1px solid var(--card-edge);
    box-shadow: 0 10px 28px rgba(0,0,0,0.45);
  }
  .card--details { left: 72px; top: 278px; display: flex; }
  .card--brand { left: 624px; top: 278px; display: flex; align-items: center; justify-content: center; }

  .brand-panel {
    width: 236px;
    display: flex;
    align-items: center;
    justify-content: center;
    border-right: 1px solid var(--divider);
  }
  .brand-name {
    font-family: "Libre Baskerville", Georgia, serif;
    color: var(--text-light);
    font-size: 19px;
    letter-spacing: 1px;
    text-transform: uppercase;
    display: flex;
    align-items: center;
    gap: 10px;
  }
  .brand-name .brand-dot {
    width: 14px; height: 14px; background: var(--accent-blue); display: inline-block;
  }
  .card--brand .brand-name { color: var(--silver); font-size: 28px; gap: 14px; }
  .card--brand .brand-dot { background: var(--silver); width: 18px; height: 18px; }

  .contact-panel {
    flex: 1;
    padding: 58px 0 0 26px;
    color: var(--text-muted);
    font-size: 13.5px;
  }
  .person-name {
    font-family: "Roboto Slab", Georgia, serif;
    font-weight: 700;
    color: var(--accent-blue);
    font-size: 15px;
    letter-spacing: 0.5px;
    text-transform: uppercase;
  }
  .person-role { margin-top: 1px; font-size: 13px; }
  .contact-list { list-style: none; margin-top: 8px; }
  .contact-list li { display: flex; align-items: center; gap: 7px; line-height: 20px; }
  .contact-list svg { width: 11px; height: 11px; fill: var(--accent-blue); flex: none; }
  .address { margin-top: 16px; line-height: 19px; }
</style>
</head>
<body>
  <section class="card card--details">
    <div class="brand-panel">
      <span class="brand-name"><span class="brand-dot"></span>Meridian Spine</span>
    </div>
    <div class="contact-panel">
      <p class="person-name">Daniel Hart</p>
      <p class="person-role">Managing Director</p>
      <ul class="contact-list">
        <li>
          <svg viewBox="0 0 12 12" aria-hidden="true"><path d="M2 1h2.5l1 3-1.5 1a6 6 0 0 0 3 3l1-1.5 3 1V10a1 1 0 0 1-1 1A9 9 0 0 1 1 2a1 1 0 0 1 1-1z"/></svg>
          041-555 208 317
        </li>
        <li>
          <svg viewBox="0 0 12 12" aria-hidden="true"><path d="M1 2.5h10v7H1z M1.5 3l4.5 3.5L10.5 3" stroke="#101010" stroke-width="0.9"/></svg>
          hello@meridianspine.com
        </li>
        <li>
          <svg viewBox="0 0 12 12" aria-hidden="true"><circle cx="6" cy="6" r="5"/><path d="M1 6h10M6 1c-2 2.5-2 7.5 0 10M6 1c2 2.5 2 7.5 0 10" stroke="#101010" stroke-width="0.8" fill="none"/></svg>
          www.meridianspine.com
        </li>
      </ul>
      <p class="address">88, Harbour Lane Suite 4<br>20931, Westland</p>
    </div>
  </section>

  <section class="card card--brand">
    <span class="brand-name"><span class="brand-dot"></span>Meridian Spine</span>
  </section>
</body>
</html>
```